Business cards for KORU Real Estate Holdings LLC

We need a cool, original business card design for a company based in the Washington DC metropolitan area. We are a new energetic and passionate Real Estate Investing Company that invests in all types of real estate; commercial, residential, industrial etc.

Our company color is Red since it reflects action, energy and speed; it is assertive confident, energizing, exciting, powerful, passionate and determined. So we would like business card communicate those qualities to the audience.

Our audiences are investors that want to invest with us, real estate sellers, buyers, and tenants who lease from us.

Our logo is attached

```html
<!DOCTYPE html>
<html lang="en">
<head>
<meta charset="utf-8">
<title>KORU Real Estate Holdings LLC — Business Cards</title>
<link href="https://fonts.googleapis.com/css2?family=Arimo:wght@400;700&display=swap" rel="stylesheet">
<style>
  :root {
    --backdrop: #d9d9d9;
    --card-red: #df1f26;
    --ink: #2b2b2b;
    --ink-soft: #3a3a3a;
    --mark-grey: #cfcfcf;
    --icon-panel: #d4d4d4;
  }
  * { box-sizing: border-box; margin: 0; padding: 0; }
  html, body {
    width: 1200px;
    height: 960px;
    overflow: hidden;
    background: var(--backdrop);
    font-family: "Arimo", Arial, sans-serif;
  }
  .sheet {
    position: relative;
    width: 1200px;
    height: 960px;
  }
  .card {
    position: absolute;
    left: 220px;
    width: 760px;
    height: 430px;
    background: var(--card-red);
    box-shadow: 0 6px 18px rgba(0,0,0,0.25);
  }
  .card--front { top: 35px; }
  .card--back { top: 495px; }

  .brand {
    display: flex;
    align-items: center;
    gap: 22px;
    color: var(--ink);
    font-weight: 700;
  }
  .brand__dot {
    flex: none;
    border-radius: 50%;
    background: var(--mark-grey);
  }
  .brand__name { line-height: 1; }
  .brand__title { display: block; letter-spacing: 0.06em; }
  .brand__subtitle { display: block; letter-spacing: 0.01em; margin-top: 10px; }

  .card--front .brand {
    position: absolute;
    left: 120px;
    top: 140px;
  }
  .card--front .brand__dot { width: 96px; height: 96px; }
  .card--front .brand__title { font-size: 104px; }
  .card--front .brand__subtitle { font-size: 27px; }

  .card--back .brand {
    position: absolute;
    left: 48px;
    top: 158px;
    gap: 14px;
  }
  .card--back .brand__dot { width: 52px; height: 52px; }
  .card--back .brand__title { font-size: 58px; }
  .card--back .brand__subtitle { font-size: 15px; margin-top: 6px; }

  .divider {
    position: absolute;
    left: 392px;
    top: 120px;
    width: 3px;
    height: 190px;
    background: var(--ink);
  }
  .contact {
    position: absolute;
    left: 412px;
    top: 124px;
    display: flex;
    gap: 14px;
  }
  .contact__icons {
    width: 30px;
    padding: 6px 0;
    background: var(--icon-panel);
    display: flex;
    flex-direction: column;
    align-items: center;
    gap: 12px;
  }
  .contact__icons svg { width: 18px; height: 18px; display: block; }
  .contact__list {
    list-style: none;
    display: flex;
    flex-direction: column;
    gap: 12px;
    padding-top: 6px;
    color: #111;
    font-size: 15.5px;
    font-weight: 400;
  }
  .contact__list li { height: 18px; line-height: 18px; }
</style>
</head>
<body>
<main class="sheet">

  <section class="card card--front" aria-label="Card front">
    <div class="brand">
      <span class="brand__dot"></span>
      <p class="brand__name">
        <span class="brand__title">KORU</span>
        <span class="brand__subtitle">Real Estate Holdings LLC</span>
      </p>
    </div>
  </section>

  <section class="card card--back" aria-label="Card back">
    <div class="brand">
      <span class="brand__dot"></span>
      <p class="brand__name">
        <span class="brand__title">KORU</span>
        <span class="brand__subtitle">Real Estate Holdings LLC</span>
      </p>
    </div>

    <div class="divider"></div>

    <div class="contact">
      <div class="contact__icons" aria-hidden="true">
        <svg viewBox="0 0 18 18"><rect x="5" y="1" width="8" height="16" rx="1.5" fill="#c21a20"/><rect x="6.5" y="3" width="5" height="10" fill="#f2f2f2"/></svg>
        <svg viewBox="0 0 18 18"><path d="M2 7c0-3 3-4 7-4s7 1 7 4l-3 1-1-2H6L5 8z" fill="#2b2b2b"/><rect x="4" y="9" width="10" height="7" rx="1" fill="#2b2b2b"/><circle cx="9" cy="12.5" r="1.8" fill="#d4d4d4"/></svg>
        <svg viewBox="0 0 18 18"><rect x="2" y="4" width="14" height="10" fill="#2b2b2b"/><path d="M2 4l7 6 7-6" fill="none" stroke="#d4d4d4" stroke-width="1.4"/></svg>
        <svg viewBox="0 0 18 18" fill="none" stroke="#2b2b2b" stroke-width="1.4"><circle cx="9" cy="9" r="7"/><ellipse cx="9" cy="9" rx="3" ry="7"/><path d="M2 9h14M3.5 5h11M3.5 13h11"/></svg>
        <svg viewBox="0 0 18 18"><path d="M9 1a5 5 0 0 1 5 5c0 4-5 10-5 10S4 10 4 6a5 5 0 0 1 5-5z" fill="#2b2b2b"/><circle cx="9" cy="6" r="1.8" fill="#c21a20"/></svg>
      </div>
      <ul class="contact__list">
        <li>202 555 0147</li>
        <li>202 555 0193</li>
        <li>info@korurealestate.com</li>
        <li>www.korurealestate.com</li>
        <li>area,state,zipcode,country</li>
      </ul>
    </div>
  </section>

</main>
</body>
</html>
```